NZ First of it's kind solutions directory and marketplace for busy Mums needs a business card design

We need a business card design for our new nationwide business in NZ (long term plans to go global). We provide solutions to the everyday challenges that busy Mums face by connecting them with quality communities and suppliers of carefully selected, relevant products and services. We sell direct via our online marketplace. The final design should communicate our values of inclusivity, quality and smart solutions. Colours should incorporate our logo colour palette of #477077 and #6ba8b2. Our website is at https://www.brightnestmums.example

Target Market(s)

busy Mums, Age 28 – 50, female, income over $100K, location main centres NZ primarily but NZ wide. Is likely juggling work or career with a young family. Probably had hobbies which have fallen by the wayside.
-Wants to succeed in her chosen career without compromising on family life
-to successfully juggle her career without feeling like she is compromising her children
- Is time poor, something always has to give and it’s generally her health (she’ll stay up late, get stressed)
- probably ex corporate or professional career. Has discretional income

Industry/Entity Type

Business

Contact Information for Business Card

Lena Forbisher, Founder, BrightNestMums.example (Strapline Tap; Gather; Sorted), 47 Kowhai Terrace, Ellerslie, Auckland 1051, New Zealand. Mob: 021 483 517 Ph: +64 (0)9 571 4860

Font styles to use
Other font styles liked:
• Raleway, and/or Architects Daughter

Colors
00a990
33b8a4
86cfc6
cfeae6

Requirements
Must have
• the above details, streamline. the logo and colours associated with those logos
Should not have
• foil or metallic colours

```html
<!DOCTYPE html>
<html lang="en">
<head>
<meta charset="utf-8">
<title>BrightNestMums – Business Card</title>
<link rel="stylesheet" href="https://fonts.googleapis.com/css2?family=Roboto:wght@400;500&family=Roboto+Condensed:wght@500;700&family=Raleway:wght@700&display=swap">
<style>
  :root {
    --stage: #2a2a2a;
    --slate: #477077;
    --slate-deep: #41636a;
    --sky: #6ba8b2;
    --mint: #00a990;
    --mint-soft: #33b8a4;
    --paper: #f1f1f1;
    --ink: #444444;
    --white: #ffffff;
  }
  html, body {
    margin: 0;
    padding: 0;
    width: 1200px;
    height: 960px;
    overflow: hidden;
    background: var(--stage);
  }
  .canvas {
    position: relative;
    width: 1200px;
    height: 960px;
  }
  .card {
    position: absolute;
    width: 600px;
    height: 342px;
    border-radius: 22px;
    overflow: hidden;
    box-shadow: 0 3px 8px rgba(0,0,0,0.45);
  }
  .card-front {
    left: 314px;
    top: 113px;
    background: linear-gradient(135deg, var(--slate) 0%, var(--slate-deep) 100%);
  }
  .card-back {
    left: 311px;
    top: 472px;
    background: var(--paper);
  }
  .accent-band {
    position: absolute;
    left: 0;
    top: 54px;
    width: 13px;
    height: 38px;
    background: var(--mint-soft);
  }
  .mint-panel {
    position: absolute;
    left: 0;
    top: 0;
  }
  .holder-name {
    position: absolute;
    left: 53px;
    top: 50px;
    margin: 0;
    font: 700 21px/1 "Roboto Condensed", sans-serif;
    color: var(--sky);
    letter-spacing: 0.2px;
  }
  .holder-role {
    position: absolute;
    left: 54px;
    top: 77px;
    margin: 0;
    font: 500 15px/1 "Roboto", sans-serif;
    color: var(--white);
  }
  .address {
    position: absolute;
    left: 54px;
    top: 193px;
    margin: 0;
    font: 400 14.5px/19px "Roboto", sans-serif;
    color: var(--white);
    font-style: normal;
  }
  .contact-list {
    position: absolute;
    left: 53px;
    top: 238px;
    margin: 0;
    padding: 0;
    list-style: none;
    font: 400 14.5px/19.5px "Roboto", sans-serif;
    color: var(--white);
  }
  .contact-list li {
    display: flex;
    align-items: center;
    gap: 8px;
  }
  .contact-icon {
    width: 14px;
    height: 14px;
    flex: none;
  }
  .brand-lockup {
    position: absolute;
    left: 0;
    right: 0;
    top: 150px;
    display: flex;
    justify-content: center;
    align-items: center;
    gap: 14px;
  }
  .brand-dot {
    width: 34px;
    height: 34px;
    border-radius: 50%;
    background: var(--slate);
  }
  .brand-name {
    font: 700 42px/1 "Raleway", sans-serif;
    color: var(--slate);
    letter-spacing: -0.5px;
  }
  .strapline {
    position: absolute;
    left: 0;
    right: 0;
    top: 287px;
    margin: 0;
    text-align: center;
    font: 400 14px/1 "Roboto", sans-serif;
    color: var(--ink);
  }
</style>
</head>
<body>
<main class="canvas">
  <section class="card card-front" aria-label="Business card front">
    <svg class="mint-panel" width="600" height="342" viewBox="0 0 600 342" aria-hidden="true">
      <defs>
        <linearGradient id="mintFade" x1="0" y1="0" x2="1" y2="1">
          <stop offset="0" stop-color="#2fb39c"/>
          <stop offset="1" stop-color="#33b8a4"/>
        </linearGradient>
      </defs>
      <polygon points="400,0 600,0 600,342 455,342" fill="url(#mintFade)"/>
    </svg>
    <div class="accent-band"></div>
    <h1 class="holder-name">LENA FORBISHER</h1>
    <p class="holder-role">FOUNDER</p>
    <address class="address">47 Kowhai Terrace, Ellerslie<br>Auckland 1051, New Zealand.</address>
    <ul class="contact-list">
      <li>
        <svg class="contact-icon" viewBox="0 0 14 14" aria-hidden="true"><path d="M3 1.5l2 2.6-1.2 1.4c.8 1.8 2 3 3.8 3.8l1.4-1.2 2.6 2-1.2 1.9C6.4 11.8 2.2 7.6 1.2 3.6z" fill="#6ba8b2"/></svg>
        <span>+64 (0)9 571 4860</span>
      </li>
      <li>
        <svg class="contact-icon" viewBox="0 0 14 14" aria-hidden="true"><rect x="3.5" y="0.8" width="7" height="12.4" rx="1.2" fill="none" stroke="#6ba8b2" stroke-width="1.4"/><circle cx="7" cy="11" r="0.8" fill="#6ba8b2"/></svg>
        <span>021 483 517</span>
      </li>
      <li>
        <svg class="contact-icon" viewBox="0 0 14 14" aria-hidden="true"><circle cx="7" cy="7" r="6" fill="#6ba8b2"/><path d="M3.5 4.5c1.5.2 2 1.3 3 1.6.8.3.4 1.6 1.3 2 .8.4.2 2-.5 3M9 2.2c-.3 1 .6 1.6 1.6 1.5" fill="none" stroke="#477077" stroke-width="1.1"/></svg>
        <span>BrightNestMums.example</span>
      </li>
    </ul>
  </section>

  <section class="card card-back" aria-label="Business card back">
    <div class="brand-lockup">
      <span class="brand-dot" aria-hidden="true"></span>
      <span class="brand-name">BrightNestMums</span>
    </div>
    <p class="strapline">Tap; Gather; Sorted</p>
  </section>
</main>
</body>
</html>
```